Design a Website for an IT Support Company

We are an IT support company that provides commercial IT support and services to small and medium sized businesses. We are in need of a website to be developed for our business.
We would like to work with someone who is either familiar with the IT field, or has developed a website for an IT support company in the past.
Some examples of designs/layouts that we like:
https://www.veldaworks.example/
http://www.marsbyquill.example/
http://817kq.example/
http://www.olbenstructures.example/
http://www.bykq.example/
I have attached a word document that gives a menu system/page layout format that we would like for our website as well as branch office phone numbers. Our logo is also attached that you can use for your design purposes. We currently do not have copy produced for all of the pages outlined in the word document, but would get this done during the project with the selected designer.
We would like the website to be SEO friendly & fully responsive. We would prefer a Wordpress format, however, we are open to HTML formats as well.

```html
<!DOCTYPE html>
<html lang="en">
<head>
<meta charset="utf-8">
<title>Stridewell IT — Commercial IT Support</title>
<link rel="stylesheet" href="https://fonts.googleapis.com/css2?family=Cabin:wght@400;600;700&family=Jura:wght@400;500&family=Mulish:wght@400;600;700&display=swap">
<style>
:root{
  --blue:#0a73c4;
  --blue-dark:#075fa6;
  --blue-deep:#0b4f8a;
  --navy:#0c1c30;
  --ink:#2a2a2a;
  --muted:#6a6a6a;
  --white:#ffffff;
  --footer:#262626;
  --footer-text:#b8b8b8;
  --card:rgba(12,116,200,0.86);
}
*{margin:0;padding:0;box-sizing:border-box}
html,body{width:1200px;height:2917px;overflow:hidden}
body{position:relative;font-family:'Mulish',sans-serif;color:var(--ink);background:var(--white)}
.abs{position:absolute}
.heading{font-family:'Jura',sans-serif;font-weight:500;font-size:46px;letter-spacing:1px}

/* top bar + nav */
.topbar{left:0;top:0;width:1200px;height:39px;background:var(--blue)}
.topbar .phone{left:806px;top:6px;color:var(--white);font-family:'Jura',sans-serif;font-size:22px;font-weight:500;display:flex;align-items:center;gap:8px}
.social-dot{border-radius:50%;border:2px solid var(--white);width:30px;height:30px;top:4px}
.navbar{left:0;top:39px;width:1200px;height:87px;background:var(--white);box-shadow:0 3px 6px rgba(0,0,0,.25);z-index:2}
.brand{display:flex;align-items:center;gap:12px;font-family:'Cabin',sans-serif;font-weight:700;font-size:34px;color:var(--ink)}
.brand .mark{width:46px;height:46px;border-radius:50%;background:var(--blue)}
.navbar .brand{left:78px;top:18px}
.nav{left:550px;top:25px;display:flex;gap:0;font-family:'Mulish',sans-serif;font-size:16px;font-weight:600;color:var(--ink)}
.nav a{color:inherit;text-decoration:none;position:absolute;top:0;white-space:nowrap;line-height:43px}
.nav .active{background:var(--blue);color:var(--white);border-radius:22px;padding:0 20px;left:0}

/* hero */
.hero{left:0;top:126px;width:1200px;height:551px;background:linear-gradient(100deg,#eef1f4 0%,#dfe4ea 45%,#a9b3bf 70%,#6d6760 100%)}
.hero .ring{left:80px;top:100px;width:56px;height:56px;border-radius:50%;border:4px solid var(--blue)}
.hero h1{left:80px;top:170px;font-family:'Cabin',sans-serif;font-weight:700;font-size:56px;line-height:68px;color:var(--white);text-shadow:0 3px 6px rgba(0,0,0,.45)}
.hero p{left:80px;top:316px;width:560px;font-size:18px;line-height:31px;color:#333}
.btn{display:flex;align-items:center;justify-content:center;border-radius:28px;font-family:'Jura',sans-serif;font-weight:500;font-size:22px;color:var(--white);letter-spacing:1px}
.hero .btn{left:80px;top:391px;width:206px;height:53px;background:var(--blue)}

/* welcome */
.welcome{left:0;top:677px;width:1200px;height:428px;background:var(--blue)}
.welcome .heading{left:80px;top:44px;color:var(--white)}
.copy{font-size:13.5px;line-height:28px}
.copy p+p{margin-top:6px}
.welcome .copy{left:80px;top:112px;width:545px;color:#e6f0fa}
.welcome .btn.outline{left:78px;top:319px;width:187px;height:50px;border:2px solid var(--white)}
.welcome .frame{left:716px;top:58px;width:406px;height:305px;border:2px solid rgba(255,255,255,.8)}
.welcome .photo{left:690px;top:83px;width:404px;height:306px;background:linear-gradient(135deg,#bfe6ff 0%,#3aa2e8 40%,#0f4f8e 80%,#0a2a52 100%)}

/* services */
.services-title{left:0;top:1160px;width:1200px;text-align:center;color:#222}
.services-band{left:0;top:1449px;width:1200px;height:263px;background:linear-gradient(90deg,#132a48 0%,#0c1c30 45%,#102540 100%)}
.card{top:1315px;width:332px;height:467px;background:var(--card)}
.card h3{position:absolute;top:80px;left:0;width:100%;text-align:center;font-family:'Jura',sans-serif;font-weight:500;font-size:22px;color:var(--white);letter-spacing:1px}
.card ul{position:absolute;top:127px;left:40px;list-style:none;color:var(--white);font-size:15px}
.card li{height:29.2px;display:flex;align-items:center;gap:12px;white-space:nowrap}
.badge{width:140px;height:140px;border-radius:50%;background:var(--white);border:4px solid var(--blue);top:1241px;display:flex;align-items:center;justify-content:center}

/* why */
.why .frame{left:78px;top:1849px;width:457px;height:306px;border:2px solid #e3e3e3}
.why .photo{left:107px;top:1877px;width:404px;height:303px;background:linear-gradient(120deg,#e9ecef 0%,#c9cfd6 50%,#8f9aa6 100%)}
.why .heading{left:568px;top:1868px;color:#222}
.why .copy{left:568px;top:1932px;width:550px;color:var(--muted)}
.why .btn{left:566px;top:2134px;width:187px;height:52px;background:var(--blue)}

/* contact */
.contact{left:0;top:2243px;width:1200px;height:334px;background:linear-gradient(90deg,#0a66b0,#0b72c2 60%,#0a5fa6)}
.contact .panel{left:78px;top:0;width:342px;height:334px;background:var(--blue-deep)}
.contact .ring{left:219px;top:92px;width:56px;height:56px;border-radius:50%;border:4px solid var(--white)}
.contact .heading{left:78px;top:190px;width:342px;text-align:center;color:var(--white)}
.office{display:flex;gap:14px;color:var(--white)}
.office .ico{width:50px;height:50px;border-radius:50%;border:2px solid var(--white);display:flex;align-items:center;justify-content:center;flex:none}
.office .solid{background:var(--white)}
.office small{display:block;font-size:13px;font-weight:700;margin-top:-2px}
.office strong{display:block;font-family:'Mulish',sans-serif;font-weight:600;font-size:22px;margin-top:2px}

/* footer */
.footer{left:0;top:2577px;width:1200px;height:340px;background:var(--footer);color:var(--footer-text)}
.footer .brand{left:78px;top:82px;color:var(--white)}
.footer .social{top:170px;width:46px;height:46px;border-radius:50%;background:var(--blue)}
.footer h4{font-family:'Mulish',sans-serif;font-weight:600;font-size:16px;color:var(--blue);letter-spacing:1px}
.sitemap{left:344px;top:32px}
.sitemap ul{list-style:none;margin-top:16px}
.sitemap li{font-size:14px;height:33px;display:flex;align-items:center;gap:12px}
.sitemap li::before{content:"";width:8px;height:8px;border-radius:50%;background:var(--blue)}
.fcontact{left:609px;top:32px;width:260px}
.frow{display:flex;gap:16px;font-size:13.5px;line-height:25px}
.frow svg{flex:none;margin-top:4px}
.newsletter{left:875px;top:32px;width:250px}
.newsletter p{font-size:13.5px;line-height:25px;margin-top:14px}
.newsletter .field{margin-top:14px;margin-left:-4px;width:251px;height:44px;background:#f1f1f1;color:#555;font-size:13px;padding:0 12px;display:flex;align-items:center}
.newsletter .btn{margin-top:10px;margin-left:-4px;width:183px;height:47px;background:var(--blue);font-size:20px}
.copyright{left:0;top:298px;width:1200px;text-align:center;font-size:13px;color:#cfcfcf}
</style>
</head>
<body>

<svg width="0" height="0" style="position:absolute">
  <defs>
    <symbol id="wifi" viewBox="0 0 20 16">
      <path d="M1 6a13 13 0 0 1 18 0M4 9a9 9 0 0 1 12 0M7 12a5 5 0 0 1 6 0" fill="none" stroke="currentColor" stroke-width="2" stroke-linecap="round"/>
      <circle cx="10" cy="14.5" r="1.4" fill="currentColor"/>
    </symbol>
    <symbol id="phone" viewBox="0 0 24 24">
      <path d="M6.6 10.8a15 15 0 0 0 6.6 6.6l2.2-2.2a1 1 0 0 1 1-.25 11.4 11.4 0 0 0 3.6.57 1 1 0 0 1 1 1V20a1 1 0 0 1-1 1A17 17 0 0 1 3 4a1 1 0 0 1 1-1h3.5a1 1 0 0 1 1 1c0 1.25.2 2.45.57 3.57a1 1 0 0 1-.25 1z" fill="currentColor"/>
    </symbol>
  </defs>
</svg>

<!-- top bar -->
<div class="abs topbar">
  <div class="abs phone"><svg width="20" height="20" style="color:#fff"><use href="#phone"/></svg>555-210-4400</div>
  <span class="abs social-dot" style="left:1010px"></span>
  <span class="abs social-dot" style="left:1053px"></span>
  <span class="abs social-dot" style="left:1092px"></span>
</div>

<header class="abs navbar">
  <div class="abs brand"><span class="mark"></span>Stridewell IT</div>
  <nav class="abs nav">
    <a class="active" href="#">HOME</a>
    <a href="#" style="left:115px">ABOUT US</a>
    <a href="#" style="left:226px">SERVICES</a>
    <a href="#" style="left:329px">WHY STRIDEWELL IT</a>
    <a href="#" style="left:496px">CONTACT</a>
  </nav>
</header>

<!-- hero -->
<section class="abs hero" role="img" aria-label="Photo of two business colleagues reviewing work at a laptop in a bright office">
  <span class="abs ring"></span>
  <h1 class="abs">Get More From Your<br>Technology</h1>
  <p class="abs">Provides Commercial It Support And Services To Small And Medium Sized Businesses</p>
  <a class="abs btn">CONTACT US</a>
</section>

<!-- welcome -->
<section class="abs welcome">
  <h2 class="abs heading">Welcome to Stridewell It</h2>
  <div class="abs copy">
    <p>Lorem Ipsum is simply dummy text of the printing and typesetting industry. Lorem Ipsum has been the industry's standard dummy text ever since the 1500s, when an unknown printer took a galley of type and scrambled it to make.</p>
    <p>A type specimen book. It has survived not only five centuries, but also the leap into electronic typesetting, remaining essentially unchanged. It was popularised in the 1960s with the release of Pressfold sheets containing Lorem Ipsum passages, and more recently with desktop publishing software like Quillset Layout.</p>
  </div>
  <a class="abs btn outline">KNOW MORE</a>
  <span class="abs frame"></span>
  <div class="abs photo" role="img" aria-label="Photo of a businessman standing in a blue digital data tunnel"></div>
</section>

<!-- services -->
<h2 class="abs heading services-title">Our Best Services</h2>
<div class="abs services-band" role="img" aria-label="Dark blue photo of data analytics screens"></div>

<div class="abs card" style="left:78px">
  <h3>DATA</h3>
  <ul>
    <li><svg width="20" height="16"><use href="#wifi"/></svg>Managed It Services</li>
    <li><svg width="20" height="16"><use href="#wifi"/></svg>It Support &amp; Consulting</li>
    <li><svg width="20" height="16"><use href="#wifi"/></svg>It Helpdesk Services</li>
    <li><svg width="20" height="16"><use href="#wifi"/></svg>Network Security</li>
    <li><svg width="20" height="16"><use href="#wifi"/></svg>Data Backup &amp; Recovery</li>
    <li><svg width="20" height="16"><use href="#wifi"/></svg>Servers &amp; Virtualization</li>
    <li><svg width="20" height="16"><use href="#wifi"/></svg>Remote Monitoring Services</li>
    <li><svg width="20" height="16"><use href="#wifi"/></svg>Wireless Networking</li>
    <li><svg width="20" height="16"><use href="#wifi"/></svg>Email &amp; Spam Threat</li>
    <li><svg width="20" height="16"><use href="#wifi"/></svg>Management</li>
    <li><svg width="20" height="16"><use href="#wifi"/></svg>Structured Cabling</li>
  </ul>
</div>
<div class="abs card" style="left:434px">
  <h3>CLOUD</h3>
  <ul>
    <li><svg width="20" height="16"><use href="#wifi"/></svg>Office Suite Migrations</li>
    <li><svg width="20" height="16"><use href="#wifi"/></svg>Cloud Platform Management Services</li>
    <li><svg width="20" height="16"><use href="#wifi"/></svg>Cloud Migration Services</li>
    <li><svg width="20" height="16"><use href="#wifi"/></svg>Hosted Virtual Servers</li>
    <li><svg width="20" height="16"><use href="#wifi"/></svg>Hosted Telephone Systems</li>
  </ul>
</div>
<div class="abs card" style="left:790px">
  <h3>VOICE</h3>
  <ul>
    <li><svg width="20" height="16"><use href="#wifi"/></svg>Open PBX Consulting</li>
    <li><svg width="20" height="16"><use href="#wifi"/></svg>Business Telephone Systems</li>
    <li><svg width="20" height="16"><use href="#wifi"/></svg>Multiple Office Phone Systems</li>
    <li><svg width="20" height="16"><use href="#wifi"/></svg>Desk Handset Telephone Systems</li>
    <li><svg width="20" height="16"><use href="#wifi"/></svg>SIP Trunks</li>
  </ul>
</div>

<div class="abs badge" style="left:173px" aria-label="Data icon">
  <svg width="70" height="70" viewBox="0 0 70 70" fill="#9aa3ad" stroke="#6b737c" stroke-width="1.5">
    <ellipse cx="30" cy="16" rx="18" ry="6"/>
    <path d="M12 16v36c0 3.3 8 6 18 6s18-2.7 18-6V16"/>
    <path d="M12 28c0 3.3 8 6 18 6s18-2.7 18-6M12 40c0 3.3 8 6 18 6s18-2.7 18-6" fill="none"/>
  </svg>
</div>
<div class="abs badge" style="left:529px" aria-label="Microphone icon">
  <svg width="60" height="70" viewBox="0 0 60 70">
    <rect x="19" y="4" width="22" height="38" rx="11" fill="#8c949c"/>
    <path d="M12 32a18 18 0 0 0 36 0" fill="none" stroke="#8c949c" stroke-width="4"/>
    <rect x="27" y="50" width="6" height="12" fill="#8c949c"/>
    <rect x="18" y="61" width="24" height="5" rx="2" fill="#8c949c"/>
  </svg>
</div>
<div class="abs badge" style="left:887px" aria-label="Cloud server icon">
  <svg width="76" height="64" viewBox="0 0 76 64">
    <path d="M18 34a12 12 0 0 1 2-24 16 16 0 0 1 30 2 11 11 0 0 1 8 22z" fill="#d5dbe1" stroke="#8c949c" stroke-width="2"/>
    <rect x="14" y="40" width="50" height="14" rx="5" fill="#6b737c"/>
    <circle cx="22" cy="47" r="2.5" fill="#fff"/>
  </svg>
</div>

<!-- why -->
<section class="why">
  <span class="abs frame"></span>
  <div class="abs photo" role="img" aria-label="Photo of two colleagues discussing documents at an office desk"></div>
  <h2 class="abs heading">Why Stridewell IT</h2>
  <div class="abs copy">
    <p>Lorem Ipsum is simply dummy text of the printing and typesetting industry. Lorem Ipsum has been the industry's standard dummy text ever since the 1500s, when an unknown printer took a galley of type and scrambled it to make.</p>
    <p>A type specimen book. It has survived not only five centuries, but also the leap into electronic typesetting, remaining essentially unchanged. It was popularised in the 1960s with the release of Pressfold sheets containing Lorem Ipsum passages, and more recently with desktop publishing software like Quillset Layout.</p>
  </div>
  <a class="abs btn">KNOW MORE</a>
</section>

<!-- contact -->
<section class="abs contact">
  <div class="abs panel"></div>
  <span class="abs ring"></span>
  <h2 class="abs heading">Contact Us</h2>

  <div class="abs office" style="left:519px;top:72px"><span class="ico solid"><svg width="22" height="22" style="color:#0a73c4"><use href="#phone"/></svg></span><div><small>Main Number :</small><strong>555-210-4400</strong></div></div>
  <div class="abs office" style="left:788px;top:72px"><span class="ico"><svg width="22" height="22" style="color:#fff"><use href="#phone"/></svg></span><div><small>Austin :</small><strong>555-318-2700</strong></div></div>
  <div class="abs office" style="left:519px;top:142px"><span class="ico"><svg width="22" height="22" style="color:#fff"><use href="#phone"/></svg></span><div><small>Houston :</small><strong>555-427-1900</strong></div></div>
  <div class="abs office" style="left:788px;top:142px"><span class="ico"><svg width="22" height="22" style="color:#fff"><use href="#phone"/></svg></span><div><small>Tulsa :</small><strong>555-536-0840</strong></div></div>
  <div class="abs office" style="left:519px;top:212px"><span class="ico"><svg width="22" height="22" style="color:#fff"><use href="#phone"/></svg></span><div><small>San Antonio :</small><strong>555-645-3300</strong></div></div>
  <div class="abs office" style="left:788px;top:212px"><span class="ico"><svg width="22" height="22" style="color:#fff"><use href="#phone"/></svg></span><div><small>Oklahoma City :</small><strong>555-754-6120</strong></div></div>
</section>

<!-- footer -->
<footer class="abs footer">
  <div class="abs brand"><span class="mark"></span>Stridewell IT</div>
  <span class="abs social" style="left:127px"></span>
  <span class="abs social" style="left:181px"></span>
  <span class="abs social" style="left:234px"></span>

  <div class="abs sitemap">
    <h4>SITEMAP</h4>
    <ul>
      <li>Home</li><li>About Us</li><li>Services</li><li>Why Stridewell IT</li><li>Contact Us</li>
    </ul>
  </div>

  <div class="abs fcontact">
    <h4>CONTACT US</h4>
    <div class="frow" style="margin-top:16px">
      <svg width="20" height="26" viewBox="0 0 20 26"><path d="M10 1a8 8 0 0 0-8 8c0 6 8 16 8 16s8-10 8-16a8 8 0 0 0-8-8z" fill="#0a73c4"/><circle cx="10" cy="9" r="3" fill="#262626"/></svg>
      <div><b style="color:#e0e0e0">Stridewell IT</b><br>101 - Lorem ipsum is the simple dummy text of printing Text.</div>
    </div>
    <div class="frow" style="margin-top:16px"><svg width="20" height="20" style="color:#0a73c4"><use href="#phone"/></svg><div>555-210-4400</div></div>
    <div class="frow" style="margin-top:18px"><svg width="20" height="16" viewBox="0 0 20 16"><rect x="1" y="2" width="18" height="13" rx="1" fill="#0a73c4"/><path d="M1 3l9 7 9-7" fill="none" stroke="#262626" stroke-width="1.6"/></svg><div>info@stridewellit.example</div></div>
  </div>

  <div class="abs newsletter">
    <h4>NEWSLETTER</h4>
    <p>Would you like to receive exclusive access to articles, white papers and our regular monthly newsletter?</p>
    <div class="field">Enter Email Id</div>
    <a class="btn">SUBSCRIBE</a>
  </div>

  <div class="abs copyright">©Stridewell IT- 2017 All Right Reserved</div>
</footer>

</body>
</html>
```